VENTURE CAPITAL GROUP BUSINESS CARD DESIGN

Venture Capital Group based in SF looking for a bold business card design. No trendy colour explosion, 3D effects etc. Just "simple" optical effects. Works on your brain, keeps your eye focused and sticks to your mind.
Target Market(s)
Technology startups
Industry/Entity Type
Venture Capital
Contact Information for Business Card
DESMOND WHITLAKE
MANAGING PARTNER
187 FENWORTH ST SAN FRANCISCO, CA 94187
415.555.0142 O
415.555.0147 F
415.555.0193 C
desmond@veldtmoorcapital.ventures

```html
<!DOCTYPE html>
<html lang="en">
<head>
<meta charset="utf-8">
<title>Veldtmoor Capital Group – Business Card</title>
<link rel="stylesheet" href="https://fonts.googleapis.com/css2?family=Merriweather:wght@300;400;700&display=swap">
<style>
  :root {
    --canvas: #a9a7a8;
    --card: #131517;
    --brand-green: #2f9a3a;
    --accent-green: #7cc242;
    --text-light: #d0d0d0;
    --text-muted: #b9b9b9;
    --mark-fill: #1d1f21;
  }
  * { margin: 0; padding: 0; box-sizing: border-box; }
  html, body {
    width: 1200px; height: 1200px; overflow: hidden;
    background: var(--canvas);
    font-family: "Merriweather", Georgia, serif;
  }
  .canvas { position: relative; width: 1200px; height: 1200px; }
  .card {
    position: absolute; left: 242px; width: 716px; height: 420px;
    background: var(--card); overflow: hidden;
  }
  .card--front { top: 118px; }
  .card--back { top: 644px; }

  .brand-circle {
    position: absolute; border-radius: 50%;
    background: radial-gradient(circle at 40% 35%, #2a2c2e 0%, var(--mark-fill) 70%);
    border: 1px solid #3a3c3e;
  }
  .wordmark { position: absolute; color: var(--brand-green); font-weight: 400; text-transform: uppercase; }
  .wordmark__name { display: block; letter-spacing: 0.02em; line-height: 1; }
  .wordmark__tag { display: block; letter-spacing: 0.5em; line-height: 1; }

  .card--front .brand-circle { left: 276px; top: 84px; width: 164px; height: 164px; }
  .card--front .wordmark { left: 0; right: 0; top: 262px; text-align: center; }
  .card--front .wordmark__name { font-size: 42px; }
  .card--front .wordmark__tag { font-size: 13px; margin-top: 8px; padding-left: 0.5em; }

  .card--back .brand-circle { left: 46px; top: 48px; width: 100px; height: 100px; }
  .card--back .wordmark { left: 166px; top: 72px; text-align: center; }
  .card--back .wordmark__name { font-size: 34px; }
  .card--back .wordmark__tag { font-size: 11px; margin-top: 6px; padding-left: 0.5em; }

  .person { position: absolute; left: 41px; top: 208px; }
  .person__name { font-size: 22px; font-weight: 700; color: var(--text-light); letter-spacing: 0.01em; }
  .person__title { font-size: 15px; font-weight: 300; color: var(--text-muted); margin-top: 6px; }

  .contact-list { position: absolute; left: 338px; top: 212px; list-style: none; }
  .contact-list li {
    display: flex; align-items: center; height: 23px;
    font-size: 16.5px; font-weight: 300; color: var(--text-light);
  }
  .contact-list svg { width: 18px; height: 16px; margin-right: 10px; fill: var(--accent-green); flex: none; }

  .divider { position: absolute; left: 333px; right: 0; top: 334px; height: 2px; background: var(--accent-green); }
  .address { position: absolute; left: 333px; top: 345px; font-size: 16.5px; font-weight: 300; color: var(--text-light); }
</style>
</head>
<body>
<main class="canvas">

  <section class="card card--front" aria-label="Card front">
    <div class="brand-circle"></div>
    <h1 class="wordmark">
      <span class="wordmark__name">Veldtmoor</span>
      <span class="wordmark__tag">Capital Group</span>
    </h1>
  </section>

  <section class="card card--back" aria-label="Card back">
    <div class="brand-circle"></div>
    <h2 class="wordmark">
      <span class="wordmark__name">Veldtmoor</span>
      <span class="wordmark__tag">Capital Group</span>
    </h2>

    <div class="person">
      <p class="person__name">Desmond Whitlake</p>
      <p class="person__title">Managing Partner</p>
    </div>

    <ul class="contact-list">
      <li>
        <svg viewBox="0 0 18 16" aria-hidden="true"><path d="M1 5c0-2 3-4 8-4s8 2 8 4v1h-4V4.5C12 4 10.5 3.5 9 3.5S6 4 5 4.5V6H1z"/><path d="M4 8l2-2h6l2 2v7H4z"/></svg>
        415.555.0142
      </li>
      <li>
        <svg viewBox="0 0 18 16" aria-hidden="true"><rect x="5" y="1" width="8" height="4"/><rect x="1" y="5" width="16" height="7" rx="1"/><rect x="5" y="10" width="8" height="5"/></svg>
        415.555.0147
      </li>
      <li>
        <svg viewBox="0 0 18 16" aria-hidden="true"><path d="M6 0h6a1 1 0 0 1 1 1v14a1 1 0 0 1-1 1H6a1 1 0 0 1-1-1V1a1 1 0 0 1 1-1zm1 2v10h4V2z"/></svg>
        415.555.0193
      </li>
      <li>
        <svg viewBox="0 0 18 16" aria-hidden="true"><path d="M1 3h16v10H1z M2 4l7 5 7-5" fill="none" stroke="#7cc242" stroke-width="1.6"/></svg>
        desmond@veldtmoorcapital.ventures
      </li>
      <li>
        <svg viewBox="0 0 18 16" aria-hidden="true"><g fill="none" stroke="#7cc242" stroke-width="1.4"><circle cx="9" cy="8" r="7"/><ellipse cx="9" cy="8" rx="3" ry="7"/><path d="M2 8h14M3 4.5h12M3 11.5h12"/></g></svg>
        www.veldtmoorcapital.ventures
      </li>
    </ul>

    <div class="divider"></div>
    <p class="address">187 Fenworth St San Francisco, CA 94187</p>
  </section>

</main>
</body>
</html>
```